Construction company business card

One side to be the logo with the company name, The other side I would like: (Tomas verbick) Project manager 41 barrow crescent hallam 52917306224783(03) 9703 2428Info@gudeljgroup.comAnd then maybe a couple dot points saying what we do:Construction (commercial & industrial) Civil construction

Anything else please contact me!
Maybe curved st one edge of the card

Target Market(s)

Older clientele

Industry/Entity Type

Construction Company

Contact Information for Business Card

Read above

Colors
3277b5
1b1b1b
9d9d9d

Requirements
Must have
• Use my logo on one side
Nice to have
• Read above
Should not have
• Read above

```html
<!DOCTYPE html>
<html lang="en">
<head>
<meta charset="utf-8">
<title>Stonecrest Property Group – Business Card</title>
<link rel="stylesheet" href="https://fonts.googleapis.com/css2?family=Source+Sans+3:wght@400;600;700&display=swap">
<style>
  :root{
    --blue:#3277b5;
    --ink:#1b1b1b;
    --grey:#9d9d9d;
    --paper:#ffffff;
    --stage:#d6d6d6;
    --text:#3a3a3a;
  }
  *{box-sizing:border-box;margin:0;padding:0}
  html,body{width:1200px;height:900px;overflow:hidden}
  body{background:var(--stage);font-family:"Source Sans 3",sans-serif;position:relative}

  .card{position:absolute;top:295px;width:540px;height:310px;overflow:hidden;
        box-shadow:0 6px 14px rgba(0,0,0,.25)}

  /* ---------- front ---------- */
  .card-front{left:40px;background:var(--ink);border-radius:155px 0 0 155px}
  .brand-mark{position:absolute;left:55px;top:75px;width:160px;height:160px;border-radius:50%;
              background:var(--blue)}
  .brand-name{position:absolute;left:240px;top:88px;width:280px;color:var(--blue);
              font-weight:700;font-size:28px;line-height:1.05;text-transform:uppercase;letter-spacing:.5px}
  .brand-name span{display:block;white-space:nowrap}
  .services{position:absolute;left:240px;top:172px;list-style:none;font-size:15px;line-height:1.4;
            color:#f2f2f2;text-transform:uppercase;letter-spacing:.3px}
  .services .detail{color:var(--blue)}

  /* ---------- back ---------- */
  .card-back{left:620px;background:var(--paper);border-radius:0 155px 155px 0}
  .edge-strip{position:absolute;left:0;top:0;width:14px;height:100%}
  .back-brand{position:absolute;left:330px;top:100px;width:180px;display:flex;flex-direction:column;align-items:center;gap:10px}
  .back-brand .dot{width:50px;height:50px;border-radius:50%;background:var(--blue)}
  .back-brand .name{color:var(--blue);font-weight:700;font-size:20px;line-height:1.05;text-align:center;text-transform:uppercase}

  .person{position:absolute;left:42px;top:40px}
  .person .name{color:var(--blue);font-weight:700;font-size:22px;text-transform:uppercase;letter-spacing:.3px}
  .person .role{color:var(--text);font-size:15px;margin-top:-2px}

  .address{position:absolute;left:42px;top:138px;color:var(--text);font-size:14px;line-height:1.3;font-style:normal}
  .contacts{position:absolute;left:42px;top:190px;list-style:none;color:var(--text);font-size:14px;line-height:1.35}
  .contacts li{display:flex;align-items:center;gap:7px}
  .contacts svg{width:12px;height:12px;flex:none}
</style>
</head>
<body>

<section class="card card-front" aria-label="Card front">
  <div class="brand-mark"></div>
  <h1 class="brand-name"><span>Stonecrest</span><span>Property Group</span></h1>
  <ul class="services">
    <li>Construction</li>
    <li class="detail">(Commercial &amp; Industrial)</li>
    <li>Civil Construction</li>
  </ul>
</section>

<section class="card card-back" aria-label="Card back">
  <svg class="edge-strip" viewBox="0 0 14 310" preserveAspectRatio="none">
    <polygon points="0,0 14,0 14,200 0,212" fill="var(--ink)"/>
    <polygon points="0,218 14,206 14,310 0,310" fill="var(--blue)"/>
  </svg>

  <div class="back-brand">
    <span class="dot"></span>
    <span class="name">Stonecrest Property Group</span>
  </div>

  <div class="person">
    <h2 class="name">Tomas Verbick</h2>
    <p class="role">Project Manager</p>
  </div>

  <address class="address">41 Barrow Crescent<br>Kelswood 5291</address>

  <ul class="contacts">
    <li>
      <svg viewBox="0 0 12 12"><path d="M2.5 1l2 2.2-1 1.3c.7 1.5 1.8 2.6 3.2 3.3l1.3-1 2.2 2-1.2 1.7C4.5 10.5 1.4 7.3.8 2.2z" fill="var(--blue)"/></svg>
      (03) 9418 6573
    </li>
    <li>
      <svg viewBox="0 0 12 12"><rect x="3" y="0.8" width="6" height="10.4" rx="1" fill="none" stroke="var(--blue)" stroke-width="1.2"/><circle cx="6" cy="9.4" r=".7" fill="var(--blue)"/></svg>
      730 622 4783
    </li>
    <li>
      <svg viewBox="0 0 12 12"><rect x=".7" y="2.2" width="10.6" height="7.6" fill="none" stroke="var(--blue)" stroke-width="1.2"/><path d="M.9 2.5L6 6.6l5.1-4.1" fill="none" stroke="var(--blue)" stroke-width="1.2"/></svg>
      Info@verbickgroup.com
    </li>
    <li>
      <svg viewBox="0 0 12 12"><circle cx="6" cy="6" r="5" fill="none" stroke="var(--blue)" stroke-width="1.1"/><ellipse cx="6" cy="6" rx="2.2" ry="5" fill="none" stroke="var(--blue)" stroke-width="1"/><path d="M1 6h10" stroke="var(--blue)" stroke-width="1"/></svg>
      www.verbickgroup.com
    </li>
  </ul>
</section>

</body>
</html>
```